A clean crisp business card for a Landscape Construction company. Designed to be easy to read contact/ info and also be appealing/interesting, unlike a traditional business card.

Industry/Entity Type

Landscape Construction

Contact Information for Business Card

Company name : Brambleford Landscape Construction, phone number: (877) 62Vista, website:Bramblefordyards.example, Email, sales@bramblefordyards.example

Requirements
Nice to have
• Luxurious finishes/ details…. Icons or emblems next to contact info
Should not have
• Clipart or general pictures

```html
<!DOCTYPE html>
<html lang="en">
<head>
<meta charset="utf-8">
<title>Brambleford Landscape Construction – Business Card</title>
<link href="https://fonts.googleapis.com/css2?family=Roboto+Condensed:wght@300;400;700&display=swap" rel="stylesheet">
<style>
  :root {
    --bg: #2a2a2a;
    --card: #141516;
    --blue: #1a7bd6;
    --green: #a6cf2d;
    --silver: #cfd2d5;
    --grey: #b9bcc0;
  }
  * { margin: 0; padding: 0; box-sizing: border-box; }
  html, body { width: 1200px; height: 874px; overflow: hidden; }
  body {
    background: var(--bg);
    font-family: "Roboto Condensed", sans-serif;
    display: flex;
    flex-direction: column;
    align-items: center;
    justify-content: center;
    gap: 34px;
  }
  .card {
    position: relative;
    width: 660px;
    height: 380px;
    background: var(--card);
    border-radius: 22px;
    box-shadow: 0 18px 40px rgba(0,0,0,.55);
    overflow: hidden;
  }
  /* Logo side */
  .brand-mark {
    position: absolute;
    left: 0; right: 0; top: 120px;
    text-align: center;
    color: var(--silver);
    font-weight: 400;
    font-size: 44px;
    letter-spacing: 1px;
    line-height: 1.1;
  }
  .brand-mark .sub { display: block; font-size: 20px; letter-spacing: 5px; text-transform: uppercase; }
  .website {
    position: absolute;
    left: 0; right: 0; bottom: 70px;
    text-align: center;
    font-size: 15px;
    letter-spacing: 1.5px;
    text-transform: uppercase;
  }
  .website .w { color: var(--blue); font-weight: 400; }
  .website .n { color: var(--green); font-weight: 700; }
  .website .d { color: var(--silver); font-weight: 300; }
  /* Contact side */
  .person { position: absolute; left: 70px; top: 110px; }
  .person-name { color: var(--blue); font-weight: 700; font-size: 30px; text-transform: uppercase; letter-spacing: .5px; }
  .person-title { color: var(--green); font-size: 15px; text-transform: uppercase; font-weight: 300; margin-top: -2px; }
  .divider {
    position: absolute; left: 70px; right: 70px; top: 180px;
    height: 2px; background: var(--blue);
  }
  .contacts { position: absolute; left: 70px; top: 200px; list-style: none; }
  .contacts li {
    display: flex; align-items: center; gap: 10px;
    color: var(--grey); font-weight: 300; font-size: 16px;
    text-transform: uppercase; margin-bottom: 6px;
  }
  .contacts svg { width: 14px; height: 14px; fill: var(--green); flex: none; }
  .company {
    position: absolute; right: 70px; top: 92px;
    text-align: right;
    color: var(--blue);
    font-weight: 400;
    font-size: 30px;
    line-height: 1.15;
  }
  .company .sub { display: block; font-size: 14px; letter-spacing: 3px; text-transform: uppercase; }
</style>
</head>
<body>
  <section class="card card-front">
    <p class="brand-mark">Brambleford<span class="sub">Landscape Construction</span></p>
    <p class="website"><span class="w">www.</span><span class="n">bramblefordyards</span><span class="d">.example</span></p>
  </section>

  <section class="card card-back">
    <div class="person">
      <h1 class="person-name">Daniel Harrow</h1>
      <p class="person-title">President</p>
    </div>
    <p class="company">Brambleford<span class="sub">Landscape Construction</span></p>
    <div class="divider"></div>
    <ul class="contacts">
      <li><svg viewBox="0 0 24 24" aria-hidden="true"><path d="M6.6 10.8a15.1 15.1 0 0 0 6.6 6.6l2.2-2.2c.3-.3.7-.4 1-.2 1.1.4 2.3.6 3.6.6.6 0 1 .4 1 1V20c0 .6-.4 1-1 1A17 17 0 0 1 3 4c0-.6.4-1 1-1h3.5c.6 0 1 .4 1 1 0 1.3.2 2.5.6 3.6.1.3 0 .7-.2 1z"/></svg>(877) 62Vista</li>
      <li><svg viewBox="0 0 24 24" aria-hidden="true"><path d="M2 5h20v14H2z M2 5l10 8 10-8" fill="none" stroke="#a6cf2d" stroke-width="2"/></svg>sales@bramblefordyards.example</li>
      <li><svg viewBox="0 0 24 24" aria-hidden="true"><circle cx="12" cy="12" r="9" fill="none" stroke="#a6cf2d" stroke-width="2"/><path d="M3 12h18M12 3c3 3 3 15 0 18M12 3c-3 3-3 15 0 18" fill="none" stroke="#a6cf2d" stroke-width="1.5"/></svg>bramblefordyards.example</li>
    </ul>
  </section>
</body>
</html>
```